Heron Loan Partners Business Card

We need a business card design for our mortgage servicing company. In addition to servicing the loans of homeowners, we help homeowners with purchasing their homes and any mortgage refinancing. We would like to see designs that use the colors in the logo attached below (gold-ish yellow and navy blue), and any other design you deem fit! The design should communicate a simpler life with smart mortgages provided by Heron.

```html
<!DOCTYPE html>
<html lang="en">
<head>
<meta charset="utf-8">
<title>Heron Loan Partners Business Card</title>
<link href="https://fonts.googleapis.com/css2?family=Open+Sans:wght@400;600;700&display=swap" rel="stylesheet">
<style>
  :root {
    --backdrop: #222222;
    --gold: #e0b03c;
    --gold-deep: #c99a2a;
    --navy: #1d1a4f;
    --ink: #111111;
    --paper: #ffffff;
  }
  * { box-sizing: border-box; margin: 0; padding: 0; }
  html, body {
    width: 1200px; height: 780px; overflow: hidden;
    background: var(--backdrop);
    font-family: "Open Sans", Arial, sans-serif;
  }
  .canvas { position: relative; width: 1200px; height: 780px; }
  .card {
    position: absolute; width: 520px; height: 300px;
    border-radius: 2px;
  }
  .card-back {
    left: 90px; top: 70px;
    background: var(--gold);
    border-bottom: 4px solid var(--gold-deep);
  }
  .card-back .back-name {
    position: absolute; right: 52px; bottom: 48px;
    color: var(--navy); font-weight: 700; font-size: 15px;
    display: flex; align-items: center; gap: 6px;
  }
  .back-name .mark-dot {
    width: 8px; height: 8px; border-radius: 50%; background: var(--navy);
  }
  .card-front {
    left: 590px; top: 400px;
    background: var(--paper);
    border-bottom: 4px solid var(--gold);
  }
  .brand {
    position: absolute; left: 34px; top: 34px;
    display: flex; align-items: center; gap: 10px;
    color: var(--navy); font-weight: 700; font-size: 26px; line-height: 1;
  }
  .brand .mark-circle {
    width: 22px; height: 22px; border-radius: 50%; background: var(--navy);
  }
  .person {
    position: absolute; left: 34px; top: 170px;
    font-size: 30px; font-weight: 700; line-height: 1;
    white-space: nowrap;
  }
  .person .first { color: var(--gold); }
  .person .last { color: var(--ink); }
  .person .role { color: var(--gold); font-weight: 400; font-size: 15px; margin-left: 6px; }
  .contacts {
    position: absolute; left: 34px; top: 218px; right: 24px;
    font-size: 12.5px; color: var(--ink); line-height: 1.7;
  }
  .contacts .row { display: flex; gap: 22px; white-space: nowrap; }
  .contacts .label { color: var(--gold); font-weight: 600; margin-right: 3px; }
</style>
</head>
<body>
<main class="canvas">
  <section class="card card-back" aria-label="Card back">
    <div class="back-name"><span class="mark-dot"></span>Heron</div>
  </section>

  <section class="card card-front" aria-label="Card front">
    <div class="brand"><span class="mark-circle"></span>Heron Loan Partners</div>
    <h1 class="person">
      <span class="first">Alena</span> <span class="last">Dvorakova</span><span class="role">CEO</span>
    </h1>
    <div class="contacts">
      <div class="row">
        <span><span class="label">T:</span>(555) 014-3692</span>
        <span><span class="label">E:</span>info@website.com</span>
        <span><span class="label">W:</span>www.website.com</span>
      </div>
      <div class="row">
        <span>1840 Brookline Ave. Suite 300 Riverton, TX 75010</span>
      </div>
    </div>
  </section>
</main>
</body>
</html>
```